Business Card Design

Online clothing womens clothing store, I sell my clothing online and at the markets.

i would like the attached picture on the front of the card and the contact information on the back.

Industry/Entity Type

Business

Contact Information for Business Card

Marlow Thread
Karen Whitfield
(Instagram symbol) _marlow_thread_
(Facebook symbol) www.fakebookexample.com/marlowthreadau/

W : www.marlowthread.example.au
E : info@marlowthread.example.au
P : 0498716204

```html
<!DOCTYPE html>
<html lang="en">
<head>
<meta charset="utf-8">
<title>Marlow Thread – Business Card</title>
<link rel="stylesheet" href="https://fonts.googleapis.com/css2?family=Raleway:wght@300;400&family=Arimo&family=Oswald:wght@600&display=swap">
<style>
  :root {
    --page: #e8e5e0;
    --card-black: #0d0d0d;
    --band-grey: #3b3b3b;
    --ink-white: #ffffff;
    --ink-soft: #e6e6e6;
    --mist-light: #dcdcdc;
    --mist-mid: #9a9a9a;
    --mist-dark: #3e3e3e;
  }
  * { box-sizing: border-box; margin: 0; padding: 0; }
  html, body { width: 1200px; height: 858px; overflow: hidden; background: var(--page); }
  .canvas { position: relative; width: 1200px; height: 858px; }

  .card {
    position: absolute;
    width: 540px;
    height: 330px;
    top: 264px;
    overflow: hidden;
    box-shadow: 0 8px 22px rgba(0,0,0,0.22);
  }

  /* Contact side */
  .card-back { left: 40px; background: var(--card-black); color: var(--ink-white); }
  .brand-mark {
    position: absolute; left: 14px; top: 196px; width: 236px;
    text-align: right;
    font-family: "Raleway", sans-serif; font-weight: 300;
    font-size: 19px; letter-spacing: 3px; text-transform: uppercase;
    white-space: nowrap;
  }
  .divider {
    position: absolute; left: 262px; top: 28px;
    width: 1px; height: 200px; background: var(--ink-soft);
  }
  .holder-name {
    position: absolute; left: 280px; top: 34px;
    font-family: "Raleway", sans-serif; font-weight: 400;
    font-size: 22px; font-variant: small-caps; letter-spacing: 3px;
    white-space: nowrap;
  }
  .contact-list {
    position: absolute; left: 280px; top: 88px; list-style: none;
    font-family: "Arimo", sans-serif; font-size: 13.5px; color: var(--ink-soft);
  }
  .contact-list li { display: flex; align-items: center; height: 22px; white-space: nowrap; }
  .contact-icon {
    width: 13px; height: 13px; margin-right: 9px; flex: none; display: block;
  }
  .bottom-rule {
    position: absolute; left: 0; top: 280px; width: 100%; height: 3px; background: var(--ink-white);
  }
  .bottom-band {
    position: absolute; left: 0; top: 289px; width: 100%; height: 41px; background: var(--band-grey);
  }

  /* Picture side */
  .card-front { left: 620px; }
  .photo-area {
    position: absolute; inset: 0;
    background:
      radial-gradient(ellipse at 75% 20%, var(--mist-light) 0%, rgba(220,220,220,0) 60%),
      linear-gradient(160deg, var(--mist-light) 0%, var(--mist-mid) 45%, var(--mist-dark) 100%);
  }
  .front-wordmark {
    position: absolute; left: 26px; top: 22px;
    font-family: "Oswald", sans-serif; font-weight: 600;
    font-size: 50px; letter-spacing: 3px; text-transform: uppercase;
    color: var(--ink-white); white-space: nowrap;
  }
</style>
</head>
<body>
<div class="canvas">

  <section class="card card-back" aria-label="Contact side">
    <div class="brand-mark">Marlow Thread</div>
    <div class="divider"></div>
    <div class="holder-name">Karen Whitfield</div>
    <ul class="contact-list">
      <li>
        <svg class="contact-icon" viewBox="0 0 13 13" aria-hidden="true"><rect width="13" height="13" fill="#fff"/><path d="M4 3 l1.6 0 0.6 2 -1 0.8 a5 5 0 0 0 2 2 l0.8 -1 2 0.6 0 1.6 a1 1 0 0 1 -1 1 A6.5 6.5 0 0 1 3 4 a1 1 0 0 1 1 -1z" fill="#0d0d0d"/></svg>
        0498716204
      </li>
      <li>
        <svg class="contact-icon" viewBox="0 0 13 13" aria-hidden="true"><rect width="13" height="13" fill="#fff"/><text x="6.5" y="10" text-anchor="middle" font-family="Arimo, sans-serif" font-size="10" fill="#0d0d0d">@</text></svg>
        marlowthreadau
      </li>
      <li>
        <svg class="contact-icon" viewBox="0 0 13 13" aria-hidden="true"><rect width="13" height="13" fill="#fff"/><text x="6.5" y="10" text-anchor="middle" font-family="Arimo, sans-serif" font-size="10" fill="#0d0d0d">#</text></svg>
        marlow_thread
      </li>
      <li>
        <svg class="contact-icon" viewBox="0 0 13 13" aria-hidden="true"><rect width="13" height="13" fill="#fff"/><circle cx="6.5" cy="6.5" r="3.8" fill="none" stroke="#0d0d0d" stroke-width="1.2"/><line x1="2.7" y1="6.5" x2="10.3" y2="6.5" stroke="#0d0d0d" stroke-width="1"/></svg>
        www.marlowthread.example.au
      </li>
      <li>
        <svg class="contact-icon" viewBox="0 0 13 13" aria-hidden="true"><rect width="13" height="13" fill="#fff"/><rect x="2.5" y="3.5" width="8" height="6" fill="none" stroke="#0d0d0d" stroke-width="1.1"/><path d="M2.5 3.5 L6.5 7 L10.5 3.5" fill="none" stroke="#0d0d0d" stroke-width="1.1"/></svg>
        info@marlowthread.example.au
      </li>
    </ul>
    <div class="bottom-rule"></div>
    <div class="bottom-band"></div>
  </section>

  <section class="card card-front" aria-label="Picture side">
    <div class="photo-area" role="img" aria-label="Black and white photograph of misty mountains"></div>
    <div class="front-wordmark">Marlow Thread</div>
  </section>

</div>
</body>
</html>
```